Create modern and sleek business card for luxury real estate company

We're a "boutique" real estate office looking for a design that gets across a highly modern luxury brand. Blacks and whites are probably the best colors unless we try a silver foil for the logo. I've attached a version of our current logo here. I'd like to swap out the current font on there with Gotham Light Regular.

I'm looking to have one side of the card have the logo with the space for our agents info on the other side.

Target Market(s)

Young professionals in a "luxury" headspace

Industry/Entity Type

Real estate

Contact Information for Business Card

A place for agent name, cell number, website. The slogan "Quietly Redefining Fine Homes".

Font styles to use
Other font styles liked:
• Gotham Regular

Colors

Designer to choose only greyscale colors for use in the design.

Requirements
Must have
• Matte black as the background color. Clean lines and use of contrast. A specific design aspect that will use silver foil.
Nice to have
• Up in the air on integrating a QR code
Should not have
• Any houses or other real estate related design (ex: a clip art house)

```html
<!DOCTYPE html>
<html lang="en">
<head>
<meta charset="utf-8">
<title>Solvane Realty — Business Card</title>
<link href="https://fonts.googleapis.com/css2?family=Montserrat:wght@300;400;500&display=swap" rel="stylesheet">
<style>
  :root {
    --backdrop: #a9aaa5;
    --card-matte: #323232;
    --ink-white: #f2f2f2;
    --foil-silver: #c9c9c9;
    --rule: #d8d8d8;
  }
  * { margin: 0; padding: 0; box-sizing: border-box; }
  html, body {
    width: 1200px; height: 801px; overflow: hidden;
    background: var(--backdrop);
    font-family: "Montserrat", sans-serif;
  }
  .stage {
    position: relative; width: 1200px; height: 801px;
    display: flex; align-items: center; justify-content: center; gap: 50px;
  }
  .card {
    position: relative; width: 530px; height: 303px;
    background: var(--card-matte); border-radius: 16px;
    color: var(--ink-white);
  }
  .brand-lockup {
    position: absolute; display: flex; align-items: center; gap: 12px;
  }
  .brand-mark {
    width: 40px; height: 40px; border-radius: 50%;
    border: 2px solid var(--foil-silver); flex: none;
  }
  .brand-name {
    font-weight: 300; color: var(--foil-silver);
    letter-spacing: 0.12em; text-transform: uppercase; line-height: 1.15;
  }
  /* agent side */
  .card--agent .brand-lockup { left: 56px; top: 26px; }
  .card--agent .brand-name { font-size: 17px; }
  .agent {
    position: absolute; right: 24px; top: 132px; text-align: right;
  }
  .agent-name {
    font-weight: 500; font-size: 19px; letter-spacing: 0.04em; text-transform: uppercase;
    margin-right: 14px;
  }
  .agent-title { font-weight: 300; font-size: 12px; margin-top: 6px; letter-spacing: 0.04em; }
  .divider {
    position: absolute; left: 68px; right: 30px; top: 182px;
    height: 1px; background: var(--rule);
  }
  .contact-list {
    position: absolute; left: 76px; top: 212px; list-style: none;
    font-weight: 300; font-size: 13px; letter-spacing: 0.05em;
  }
  .contact-list li { display: flex; align-items: center; gap: 9px; line-height: 1.6; }
  .contact-list svg { width: 11px; height: 11px; fill: none; stroke: var(--ink-white); stroke-width: 1.4; }
  /* brand side */
  .card--brand .brand-lockup {
    left: 50%; top: 84px; transform: translateX(-50%); gap: 20px;
  }
  .card--brand .brand-mark { width: 88px; height: 88px; border-width: 3px; }
  .card--brand .brand-name { font-size: 34px; letter-spacing: 0.1em; }
  .slogan {
    position: absolute; left: 0; right: 0; bottom: 42px; text-align: center;
    font-weight: 400; font-size: 16px; letter-spacing: 0.12em; text-transform: uppercase;
  }
</style>
</head>
<body>
  <main class="stage">
    <section class="card card--agent" aria-label="Agent side">
      <div class="brand-lockup">
        <span class="brand-mark"></span>
        <span class="brand-name">Solvane<br>Realty</span>
      </div>
      <div class="agent">
        <p class="agent-name">Daniel Marsh</p>
        <p class="agent-title">Director</p>
      </div>
      <div class="divider"></div>
      <ul class="contact-list">
        <li><svg viewBox="0 0 12 12"><path d="M3 1.5l2 2.5-1.2 1.2a6 6 0 0 0 3 3L8 7l2.5 2-1 1.5C5.5 10.5 1.5 6.5 1.5 2.5z"/></svg>555.014.2290</li>
        <li><svg viewBox="0 0 12 12"><rect x="1" y="2.5" width="10" height="7"/><path d="M1 2.5l5 4 5-4"/></svg>info@solvanerealty.com</li>
        <li><svg viewBox="0 0 12 12"><circle cx="6" cy="6" r="5"/><path d="M1 6h10M6 1c2.5 3 2.5 7 0 10M6 1c-2.5 3-2.5 7 0 10"/></svg>www.solvanerealty.com</li>
      </ul>
    </section>
    <section class="card card--brand" aria-label="Brand side">
      <div class="brand-lockup">
        <span class="brand-mark"></span>
        <span class="brand-name">Solvane<br>Realty</span>
      </div>
      <p class="slogan">Quietly Redefining Fine Homes</p>
    </section>
  </main>
</body>
</html>
```